Private practice for psychiatry and psychotherapy needs a business card and logo

I need a logo and business card design for my private practice for psychiatry and psychotherapy. The optional names for my practice are: Vorsteling Praktijk voor Psychiatrie en Psychotherapie, or short: Praktijk Vorsteling.
I am a (child and adolescent) psychiatrist and psychotherapist. I diagnose and treat infants, children, adolescents and adults with psychiatric symptoms/disorders. I also give supervision to colleagues about their own treatments. My work is characterised by personal involvement, transparence, creativity and professionality.
I would like to have an appealing, light and bright, yet basic design that invites people (both children and adults) to contact me, gives trust and hope, without loosing professional appearance.
I uploaded my contact information which should not necessarily be all included (in this form) on the card as long as people know how to contact me. Please feel free to be creative!
Please note that my website is only temporarely and need a new design and update too!

Target Market(s)

Clients and patients (children, adolescents, adults) with psychiatric symptoms who need diagnosis and treatment. I work with private clients and patients through medical insurances.

Industry/Entity Type

Mental Health

Contact Information for Business Card

Dr. Ilse Vorsteling-ter Haaf
Psychiater/Kinder- en Jeugdpsychiater
Jorisvan Heultstraat 14
3071 PW Rotterdam
t: 06-58190274
e: info@praktijkvorsteling.nl
i: www.praktijkvorsteling.nl

Logo Text

Praktijk Vorsteling voor Psychiatrie en Psychotherapie; or short: Praktijk Vorsteling

Font styles to use
Sans Serif
Other font styles liked:
• up to designer

Requirements
Must have
• Appealing, light, bright, creative, trustful, professional and unique.

```html
<!DOCTYPE html>
<html lang="nl">
<head>
<meta charset="utf-8">
<title>Praktijk Vorsteling – visitekaartje</title>
<link rel="stylesheet" href="https://fonts.googleapis.com/css2?family=Exo+2:wght@400;500&family=Open+Sans:wght@400;600;700&display=swap">
<style>
  :root {
    --stage: #2d3235;
    --paper: #ffffff;
    --coral: #fd6b45;
    --sun: #fdf64a;
    --ocean: #0071bb;
    --ink: #2a1b1b;
    --card-w: 360px;
    --card-h: 580px;
  }
  * { margin: 0; padding: 0; box-sizing: border-box; }
  html, body {
    width: 1200px; height: 938px; overflow: hidden;
    background: var(--stage);
    font-family: "Open Sans", sans-serif;
  }
  .sheet {
    width: 1200px; height: 938px;
    display: flex; align-items: center; justify-content: center; gap: 80px;
  }
  .card {
    position: relative;
    width: var(--card-w); height: var(--card-h);
    background: var(--paper);
    border-radius: 22px;
    overflow: hidden;
    box-shadow: 0 14px 30px rgba(0,0,0,.35);
  }
  .card__shapes { position: absolute; inset: 0; width: 100%; height: 100%; }
  .band-sun { fill: var(--sun); }
  .band-coral { fill: var(--coral); }
  .band-ocean { fill: var(--ocean); }

  .brand { position: absolute; left: 0; right: 0; text-align: center; }
  .brand__dot {
    display: block; margin: 0 auto;
    border-radius: 50%; background: var(--coral);
  }
  .brand__name {
    display: block; color: var(--ink);
    font-weight: 600; text-transform: uppercase; letter-spacing: .04em;
    line-height: 1.1;
  }
  .card--front .brand { top: 110px; }
  .card--front .brand__dot { width: 70px; height: 70px; margin-bottom: 20px; }
  .card--front .brand__name { font-size: 28px; }

  .card--back .brand { top: 28px; }
  .card--back .brand__dot { width: 50px; height: 50px; margin-bottom: 12px; }
  .card--back .brand__name { font-size: 22px; }

  .person { position: absolute; left: 24px; top: 236px; color: var(--paper); }
  .person__suffix { font-size: 12px; letter-spacing: .04em; text-transform: uppercase; line-height: 18px; }
  .person__name { font-size: 19px; font-weight: 700; color: var(--sun); text-transform: uppercase; line-height: 26px; }
  .person__role { font-size: 14px; line-height: 20px; }

  .contact {
    position: absolute; right: 24px; top: 388px;
    text-align: right; color: var(--paper);
  }
  .contact__address { font-size: 14px; line-height: 21px; margin-bottom: 8px; }
  .contact__phone {
    font-family: "Exo 2", sans-serif; font-weight: 400;
    font-size: 38px; line-height: 44px; color: var(--sun); letter-spacing: .02em;
  }
  .contact__line { font-size: 14px; line-height: 21px; }
</style>
</head>
<body>
<main class="sheet">

  <section class="card card--front" aria-label="Voorzijde visitekaartje">
    <svg class="card__shapes" viewBox="0 0 360 580" preserveAspectRatio="none" aria-hidden="true">
      <path class="band-sun" d="M0,464 Q180,472 360,331 L360,580 L0,580 Z"/>
      <path class="band-coral" d="M0,493 Q180,502 360,334 L360,580 L0,580 Z"/>
    </svg>
    <div class="brand">
      <span class="brand__dot"></span>
      <span class="brand__name">Praktijk<br>Vorsteling</span>
    </div>
  </section>

  <section class="card card--back" aria-label="Achterzijde visitekaartje">
    <svg class="card__shapes" viewBox="0 0 360 580" preserveAspectRatio="none" aria-hidden="true">
      <path class="band-ocean" d="M0,139 Q180,215 360,238 L360,580 L0,580 Z"/>
      <path class="band-sun" d="M0,406 Q150,360 360,238 L360,580 L0,580 Z"/>
      <path class="band-coral" d="M0,429 Q160,378 360,242 L360,580 L0,580 Z"/>
    </svg>
    <div class="brand">
      <span class="brand__dot"></span>
      <span class="brand__name">Praktijk<br>Vorsteling</span>
    </div>
    <div class="person">
      <p class="person__suffix">ter Haaf</p>
      <p class="person__name">Dr. Ilse Vorsteling</p>
      <p class="person__role">Psychiater/kinder- en</p>
      <p class="person__role">jeugdpsychiater</p>
    </div>
    <div class="contact">
      <p class="contact__address">Jorisvan Heultstraat 14<br>3071 PW Rotterdam</p>
      <p class="contact__phone">06-58190274</p>
      <p class="contact__line">info@praktijkvorsteling.nl</p>
      <p class="contact__line">www.praktijkvorsteling.nl</p>
    </div>
  </section>

</main>
</body>
</html>
```